2017 New Year Membership Sale

I require a flyer to be designed for a mail box drop.

We are a 24/7 Gym and will be running a sale in January. No Joining Fee, Flexible membership options.

We are also going to have an open day on Saturday the 21st of January, everyone is welcome. Supplement samples and information. Free health measurements. Free starter PT pack if you join on the day.

We offer a 24/7 DIY gym as well as a comprehensive Personal Training Studio.

I have included the design I used last year.

Target Market(s)

Potential Members of all ages.

Industry/Entity Type

Gym

Requirements
Must have
• Our Address, Phone Number.
• Staffed Hours;
• Mon-Thur: 12pm - 7pm
• Fri-Sat: 8am - 1pm

```html
<!DOCTYPE html>
<html lang="en">
<head>
<meta charset="utf-8">
<title>Pacer Fitness – January Membership Sale Flyer</title>
<link href="https://fonts.googleapis.com/css2?family=Montserrat:wght@500;600;700&family=Oswald:wght@700&display=swap" rel="stylesheet">
<style>
  :root {
    --ink: #131316;
    --ink-soft: #1e1f24;
    --orange: #ee7d22;
    --teal: #1f8d9e;
    --white: #ffffff;
    --muted: #d8dadd;
    --page: #ececec;
  }
  * { margin: 0; padding: 0; box-sizing: border-box; }
  html, body { width: 1200px; height: 900px; overflow: hidden; }
  body { background: var(--page); font-family: "Montserrat", Arial, sans-serif; }

  .flyer {
    position: absolute; left: 296px; top: 22px;
    width: 607px; height: 855px;
    background: var(--ink);
    overflow: hidden;
    box-shadow: 0 6px 18px rgba(0,0,0,.25);
  }
  .flyer-art { position: absolute; inset: 0; }

  .headline {
    position: absolute; left: -6px; top: 108px;
    width: 330px;
    transform: rotate(-45deg);
    transform-origin: center;
    font-family: "Oswald", Impact, sans-serif;
    font-weight: 700; text-transform: uppercase;
    font-size: 50px; line-height: 0.95; letter-spacing: 0.5px;
    color: var(--white); text-align: center;
  }
  .headline .accent { color: var(--orange); }

  .open-hours-badge {
    position: absolute; left: 60px; top: 324px;
    font-weight: 700; font-size: 31px; line-height: 0.95;
    color: var(--muted); letter-spacing: 1px;
  }

  .welcome {
    position: absolute; left: 345px; top: 420px;
    font-weight: 600; font-size: 32px; line-height: 0.92;
    color: var(--teal); letter-spacing: 1.5px; text-transform: uppercase;
  }
  .perks {
    position: absolute; left: 346px; top: 490px;
    list-style: none; color: var(--white);
    font-weight: 600; font-size: 13.5px; line-height: 16.5px;
    text-transform: uppercase; letter-spacing: .3px;
  }
  .perks li { position: relative; padding-left: 17px; margin-bottom: 9px; }
  .perks li::before {
    content: ""; position: absolute; left: 0; top: 4px;
    width: 10px; height: 10px; border-radius: 50%; background: var(--teal);
  }

  .staffed-hours { position: absolute; left: 353px; top: 675px; color: var(--white); }
  .staffed-hours h2 {
    font-weight: 600; font-size: 18px; color: var(--teal);
    letter-spacing: 1px; text-transform: uppercase; margin-bottom: 3px;
  }
  .staffed-hours p { font-weight: 600; font-size: 15.5px; line-height: 20px; }

  .call-to-action { position: absolute; left: 347px; top: 770px; color: var(--orange); }
  .call-to-action .label { font-weight: 600; font-size: 24px; letter-spacing: 1px; line-height: 1; text-transform: uppercase; }
  .call-to-action .phone { font-weight: 700; font-size: 47px; line-height: 1; letter-spacing: 1px; }

  .open-day {
    position: absolute; left: 177px; top: 574px;
    width: 156px; height: 156px; border-radius: 50%;
    background: radial-gradient(circle at 45% 40%, #3a3a3c, #1b1b1d 70%);
    border: 3px solid var(--white);
    display: flex; flex-direction: column; align-items: center; justify-content: center;
    color: var(--orange); text-transform: uppercase; text-align: center;
  }
  .open-day .title { font-weight: 600; font-size: 19px; letter-spacing: 1px; }
  .open-day .date { font-weight: 700; font-size: 12.5px; line-height: 16px; }
  .open-day sup { font-size: 7px; }

  .brand { position: absolute; left: 14px; top: 762px; color: var(--white); }
  .brand .name { font-weight: 700; font-size: 27px; letter-spacing: .5px; line-height: 1; }
  .brand .suburb { font-weight: 500; font-size: 17px; letter-spacing: 9px; margin-top: 34px; }
</style>
</head>
<body>
  <main class="flyer">
    <svg class="flyer-art" width="607" height="855" viewBox="0 0 607 855" aria-hidden="false">
      <defs>
        <linearGradient id="rowerTone" x1="0" y1="0" x2="1" y2="1">
          <stop offset="0" stop-color="#2b3340"/>
          <stop offset=".55" stop-color="#1a1e26"/>
          <stop offset="1" stop-color="#3a3633"/>
        </linearGradient>
        <linearGradient id="gymFloorTone" x1="0" y1="0" x2="0" y2="1">
          <stop offset="0" stop-color="#d9dde0"/>
          <stop offset="1" stop-color="#8f979c"/>
        </linearGradient>
        <linearGradient id="mapTone" x1="0" y1="0" x2="1" y2="1">
          <stop offset="0" stop-color="#ecebe6"/>
          <stop offset="1" stop-color="#d6d4cd"/>
        </linearGradient>
        <linearGradient id="tealGlass" x1="0" y1="0" x2="0" y2="1">
          <stop offset="0" stop-color="#2a8494" stop-opacity=".55"/>
          <stop offset="1" stop-color="#2a6c78" stop-opacity=".75"/>
        </linearGradient>
      </defs>

      <!-- hero photo area -->
      <polygon points="345,0 607,0 607,385 0,385" fill="url(#rowerTone)" role="img" aria-label="Photo of a man training on a rowing machine in the gym"/>
      <polygon class="glass-panel" points="345,0 0,385 210,385" fill="url(#tealGlass)"/>

      <!-- lower left photos -->
      <polygon points="0,385 335,385 215,545 0,545" fill="url(#gymFloorTone)" role="img" aria-label="Photo of the gym floor with treadmills and cross trainers"/>
      <polygon points="0,545 215,545 125,660 0,750" fill="url(#mapTone)" role="img" aria-label="Street map showing the gym location"/>
      <path class="map-pin" d="M65 603 a5 5 0 1 1 10 0 c0 4 -5 9 -5 9 c0 0 -5 -5 -5 -9z" fill="#d8322c"/>

      <!-- orange stripe and corner -->
      <polygon class="accent-stripe" points="335,385 378,385 150,660 125,660" fill="var(--orange)"/>
      <polygon class="accent-corner" points="0,760 128,660 302,855 0,855" fill="var(--orange)"/>
    </svg>

    <h1 class="headline">Huge <span class="accent">Sale</span><br>In <span class="accent">January</span></h1>
    <div class="open-hours-badge">24/7<br>OPEN</div>

    <h2 class="welcome">Everyone<br>is welcome</h2>
    <ul class="perks">
      <li>No joining fee</li>
      <li>Flexible<br>membership options</li>
      <li>Supplement samples<br>and information</li>
      <li>Free measurements</li>
      <li>Free starter PT pack</li>
    </ul>

    <section class="staffed-hours">
      <h2>Staffed hours</h2>
      <p>Monday-Thursday: 12pm - 7pm</p>
      <p>Friday-Saturday: 8am - 1pm</p>
    </section>

    <section class="call-to-action">
      <div class="label">Call us now</div>
      <div class="phone">35550142</div>
    </section>

    <div class="open-day">
      <span class="title">Open Day</span>
      <span class="date">On Saturday 21<sup>st</sup><br>January</span>
    </div>

    <div class="brand">
      <div class="name">PACER FITNESS</div>
      <div class="suburb">KELLERTON</div>
    </div>
  </main>
</body>
</html>
```